Letterhead and matching envelope design for a dental office

We need a new stationary design, letterhead and envelope #10, for a dental office in Denver area. We are called Bright Harbor Dental. We want a simple and minimalistic design but not a boring design. I wish to have one good point that makes it look professional. I have attached our logo. Feel free to use either one. I want the design for letterhead and envelope look like a "matching pair" but not look the same. The envelope doesn't have to be white and it will have an address window on bottom left.

Target Market(s)

everyone who visits dentist (adults)

Industry/Entity Type

Dental

Font styles to use
Other font styles liked:
• close to font on logo or something that matches well

Requirements
Must have
• professional
• simple, minimalistic
• unique point that stands out
Nice to have
• matching but not same design for letterhead and envelope
Should not have
• not look like all the other boring designs
• no flowery, distracting feats

```html
<!DOCTYPE html>
<html lang="en">
<head>
<meta charset="utf-8">
<title>Bright Harbor Dental – Envelope #10</title>
<link href="https://fonts.googleapis.com/css2?family=Open+Sans:wght@400;600;700&display=swap" rel="stylesheet">
<style>
  :root {
    --green: #3bb54a;
    --paper: #ffffff;
    --ink: #2b2b2b;
    --backdrop: #ececec;
    --edge: #dcdcdc;
  }
  * { box-sizing: border-box; margin: 0; padding: 0; }
  html, body {
    width: 1200px;
    height: 795px;
    overflow: hidden;
    background: var(--backdrop);
    font-family: "Open Sans", Arial, sans-serif;
  }
  .canvas {
    position: relative;
    width: 1200px;
    height: 795px;
  }
  .envelope {
    position: absolute;
    left: 180px;
    width: 840px;
    height: 365px;
    background: var(--paper);
    border: 1px solid var(--edge);
    overflow: hidden;
  }
  .envelope--front { top: 25px; }
  .envelope--back { top: 405px; }

  /* Wordmark */
  .wordmark {
    position: absolute;
    left: 0;
    right: 0;
    text-align: center;
    font-weight: 600;
    font-size: 15px;
    letter-spacing: 4px;
    line-height: 1.5;
    text-transform: uppercase;
    color: var(--green);
  }
  .envelope--front .wordmark { top: 92px; }

  /* Front: divider + return address */
  .divider {
    position: absolute;
    left: 22px;
    right: 22px;
    top: 232px;
    height: 1px;
    background: var(--green);
  }
  .return-address {
    position: absolute;
    left: 82px;
    top: 244px;
    font-size: 11.5px;
    line-height: 1.55;
    color: var(--ink);
  }
  .return-address .company {
    color: var(--green);
    font-weight: 700;
    padding-left: 70px;
  }
  .contact-row {
    display: flex;
    align-items: center;
    gap: 4px;
  }
  .contact-row .icon {
    width: 11px;
    height: 11px;
    flex: none;
  }
  .contact-row .gap { width: 6px; }

  /* Front: bottom band with web tab */
  .bottom-band {
    position: absolute;
    left: 0;
    right: 0;
    bottom: 0;
    height: 8px;
    background: var(--green);
  }
  .web-tab {
    position: absolute;
    left: 44px;
    bottom: 0;
    width: 240px;
    height: 30px;
    background: var(--green);
    border-radius: 12px 12px 0 0;
    color: var(--paper);
    font-size: 12px;
    line-height: 30px;
    text-align: center;
    letter-spacing: 0.3px;
  }

  /* Back: rounded flap band */
  .flap-band {
    position: absolute;
    left: 0;
    right: 0;
    top: 0;
    height: 78px;
    background: var(--green);
    border-bottom-right-radius: 64px;
  }
  .envelope--back .wordmark {
    top: 14px;
    font-size: 12px;
    letter-spacing: 3px;
    color: var(--paper);
  }
</style>
</head>
<body>
<main class="canvas">

  <section class="envelope envelope--front" aria-label="Envelope front">
    <div class="wordmark">Bright Harbor<br>Dental</div>
    <div class="divider"></div>
    <address class="return-address" style="font-style:normal">
      <div class="company">Bright Harbor Dental</div>
      <div>4827 LAKEVIEW DR, SUITE 210 ARVADA, CO 80002</div>
      <div class="contact-row">
        <svg class="icon" viewBox="0 0 12 12" aria-hidden="true">
          <circle cx="6" cy="6" r="6" fill="var(--green)"/>
          <path d="M4 3.2 L5 3 L5.6 4.6 L4.9 5.1 Q5.5 6.6 6.9 7.1 L7.4 6.4 L9 7 L8.8 8 Q6.8 9 5 7 Q3.2 5.2 4 3.2Z" fill="#fff"/>
        </svg>
        <span>720-555-0148</span>
        <span class="gap"></span>
        <svg class="icon" viewBox="0 0 12 12" aria-hidden="true">
          <circle cx="6" cy="6" r="6" fill="var(--green)"/>
          <rect x="3" y="4" width="6" height="4.2" fill="#fff"/>
          <path d="M3 4 L6 6.4 L9 4" fill="none" stroke="var(--green)" stroke-width="0.7"/>
        </svg>
        <span>info@brightharbordental.com</span>
      </div>
    </address>
    <div class="bottom-band"></div>
    <div class="web-tab">www.brightharbordental.com</div>
  </section>

  <section class="envelope envelope--back" aria-label="Envelope back">
    <div class="flap-band"></div>
    <div class="wordmark">Bright Harbor<br>Dental</div>
  </section>

</main>
</body>
</html>
```